Business Card Design for company

We want new business cards. We'd like something different-- yet still highly professional. Our tagline is Providing leadership, delivering success. Stock photos are ok, as long as they are relevant and look upscale.

Target Market(s)

Architecture/Business Management Consulting/Engineering Consulting

Contact Information for Business Card

dark gray background with pops of blue might be good, but you tell me. You're the designers. Rounded corners might be nice, but again, you tell me.

Font styles to use
Serif
Sans Serif

Colors
3276b5
5c5c5c
9d9d9d
fbfbfb

Requirements
Nice to have
• Something different, but still very professional.

```html
<!DOCTYPE html>
<html lang="en">
<head>
<meta charset="utf-8">
<title>Norvale Partners – Business Card</title>
<link rel="stylesheet" href="https://fonts.googleapis.com/css2?family=Work+Sans:wght@400;500;600&display=swap">
<style>
  :root {
    --blue: #1f5b96;
    --ink: #3b3f48;
    --slate: #3d424d;
    --grey: #5c5c5c;
    --light: #d0d2d6;
    --paper: #fbfbfb;
    --stage: #e4e5e8;
  }
  * { margin: 0; padding: 0; box-sizing: border-box; }
  html, body { width: 1200px; height: 900px; overflow: hidden; }
  body {
    background: var(--stage);
    font-family: "Work Sans", Arial, sans-serif;
    display: flex; flex-direction: column; align-items: center; justify-content: center;
    gap: 40px;
  }
  .card {
    width: 700px; height: 400px; position: relative; overflow: hidden;
    box-shadow: 0 10px 28px rgba(0,0,0,.22);
  }
  /* front */
  .card-front { background: var(--paper); }
  .holder { position: absolute; left: 48px; top: 52px; }
  .holder-name { color: var(--blue); font-size: 27px; font-weight: 500; letter-spacing: 2px; text-transform: uppercase; }
  .holder-role { color: var(--grey); font-size: 15px; margin-top: 2px; }
  .divider { position: absolute; left: 48px; top: 132px; width: 560px; height: 1.5px; background: var(--blue); }
  .contact { position: absolute; left: 48px; top: 150px; list-style: none; color: var(--ink); font-size: 16px; }
  .contact li { display: flex; align-items: center; gap: 10px; margin-bottom: 8px; white-space: nowrap; }
  .contact svg { width: 12px; height: 12px; fill: var(--blue); flex: none; }
  .brand { position: absolute; right: 56px; top: 226px; display: flex; align-items: center; gap: 12px; white-space: nowrap; }
  .brand-mark { width: 18px; height: 18px; background: var(--blue); flex: none; }
  .brand-name { color: var(--ink); font-size: 28px; font-weight: 600; letter-spacing: 3px; text-transform: uppercase; }
  .address { position: absolute; right: 56px; bottom: 64px; text-align: right; color: var(--ink); font-size: 16px; line-height: 1.35; }
  .footer-band { position: absolute; left: 0; right: 0; bottom: 0; height: 36px; display: flex; align-items: stretch; }
  .footer-band .band-slate { background: var(--slate); }
  .footer-band .band-left { flex: 1; }
  .footer-band .band-web { background: var(--blue); color: var(--paper); font-size: 17px; font-weight: 500; padding: 0 18px; display: flex; align-items: center; margin: 0 8px; }
  .footer-band .band-right { width: 34px; }
  /* back */
  .card-back { background: var(--slate); display: flex; flex-direction: column; align-items: center; justify-content: center; gap: 48px; }
  .card-back .brand { position: static; }
  .card-back .brand-name { color: var(--light); font-size: 40px; }
  .card-back .brand-mark { width: 24px; height: 24px; }
  .web-rule { display: flex; align-items: center; gap: 16px; color: var(--light); font-size: 16px; letter-spacing: .5px; }
  .web-rule span { width: 110px; height: 1px; background: var(--light); opacity: .7; }
</style>
</head>
<body>
  <section class="card card-front">
    <div class="holder">
      <p class="holder-name">Daniel Reyes</p>
      <p class="holder-role">Director</p>
    </div>
    <div class="divider"></div>
    <ul class="contact">
      <li><svg viewBox="0 0 24 24" aria-hidden="true"><path d="M6.6 10.8a15.1 15.1 0 0 0 6.6 6.6l2.2-2.2a1 1 0 0 1 1-.25 11.4 11.4 0 0 0 3.6.57 1 1 0 0 1 1 1V20a1 1 0 0 1-1 1A17 17 0 0 1 3 4a1 1 0 0 1 1-1h3.5a1 1 0 0 1 1 1 11.4 11.4 0 0 0 .57 3.6 1 1 0 0 1-.25 1z"/></svg>(555) 014-2290</li>
      <li><svg viewBox="0 0 24 24" aria-hidden="true"><path d="M2 5h20v14H2zm2 2v.5l8 5 8-5V7zm0 2.8V17h16V9.8l-8 5z"/></svg>info@norvalepartners.com</li>
    </ul>
    <div class="brand">
      <span class="brand-mark"></span>
      <span class="brand-name">Norvale Partners</span>
    </div>
    <p class="address">214b Harbour Lane,<br>Lakeford, NZ, 4102</p>
    <div class="footer-band">
      <div class="band-slate band-left"></div>
      <div class="band-web">www.norvalepartners.com</div>
      <div class="band-slate band-right"></div>
    </div>
  </section>

  <section class="card card-back">
    <div class="brand">
      <span class="brand-mark"></span>
      <span class="brand-name">Norvale Partners</span>
    </div>
    <div class="web-rule"><span></span>www.norvalepartners.com<span></span></div>
  </section>
</body>
</html>
```